Provide bookkeeping and accounting services to small and growing businesses

We need website and logo design using the name Dornaby as the logo.
The target audience are small companies and startups who need:
1) Simple bookkeeping services
2) Accounting advice that only someone with many years of senior financial experience as a CPA can provide.

The services are provided by two individuals. each of whom specialize in one of the areas.

We want the website to be clean without a lot of visual distraction but don't know how to make a boring subject interesting. We believe our potential clients, small business owners, need to find what they want quickly and easily without a lot of verbiage or distractions.

We've attached a draft of the homepage and have completed the text on most of the other pages.

Target Market(s)

small and early stage growth companies in San Diego North County

Industry/Entity Type

Accounting

Number of Pages Required

1 page

Font styles to use
Sans Serif

Colors
86cfc6
33b8a4
85cae6

Requirements
Must have
• We need a design for the website homepage that includes the name Dornaby as the logo. Must include a design for the name.
• Must have color in teal or greenish blue.
Nice to have
• White background, clean, clear, uncluttered.
• We would like to use the design in a Theme on a WordPress website. Themes Paper Lantern and Quiet Harbour are appealing to us.
Should not have
• Moving pictures

```html
<!DOCTYPE html>
<html lang="en">
<head>
<meta charset="utf-8">
<title>Dornaby Bookkeeping</title>
<link href="https://fonts.googleapis.com/css2?family=Open+Sans:wght@300;400;600;700&display=swap" rel="stylesheet">
<style>
:root{
  --teal:#33b8a4;
  --teal-soft:#86cfc6;
  --sky:#85cae6;
  --ink:#333a3d;
  --muted:#7a8186;
  --line:#e3e6e8;
  --pale:#f4f6f7;
  --footer:#2e3335;
  --footer-deep:#24282a;
  --white:#ffffff;
}
*{box-sizing:border-box;margin:0;padding:0}
html,body{width:1200px;height:2376px;overflow:hidden}
body{font-family:"Open Sans",Arial,sans-serif;color:var(--ink);background:var(--white);font-size:13px;line-height:1.6}
.accent{color:var(--teal)}

/* Hero */
.hero{position:relative;height:540px;overflow:hidden}
.hero-photo{position:absolute;inset:0;background:linear-gradient(160deg,#5d6a6e 0%,#3b4548 45%,#2a3133 100%)}
.hero-shade{position:absolute;inset:0;background:rgba(20,26,28,.35)}
.site-header{position:relative;display:flex;justify-content:space-between;align-items:center;padding:0 60px;height:84px}
.brand-name{font-size:30px;font-weight:600;color:var(--teal);line-height:1}
.brand-tag{font-size:12px;letter-spacing:3px;text-transform:uppercase;color:var(--white);margin-top:4px}
.main-nav{display:flex;gap:38px}
.main-nav a{color:var(--white);text-decoration:none;font-size:14px;padding:28px 0 26px;border-bottom:3px solid transparent}
.main-nav a.active{color:var(--teal);border-bottom-color:var(--teal)}
.hero-copy{position:relative;text-align:center;color:var(--white);margin-top:178px}
.hero-copy h1{font-size:40px;font-weight:400;line-height:1.2}
.hero-copy p{font-size:15px;font-weight:300;margin-top:6px}
.btn-hero{display:inline-block;margin-top:22px;background:var(--teal);color:var(--white);font-size:14px;padding:10px 30px;border-radius:22px}

/* About */
.about{display:flex;gap:80px;padding:62px 60px 0;height:370px}
.about-text{width:560px}
.section-title{font-size:30px;font-weight:400;line-height:1.2}
.about-text p{color:var(--muted);margin-top:14px}
.btn-small{display:inline-block;margin-top:18px;border:1px solid var(--line);background:var(--pale);color:var(--muted);font-size:12px;padding:5px 16px;border-radius:3px}
.features{flex:1;display:flex;flex-direction:column;gap:22px}
.feature{display:flex;gap:20px;align-items:flex-start}
.feature-icon{flex:none;width:46px;height:46px;border-radius:4px;background:var(--teal);display:flex;align-items:center;justify-content:center}
.feature h3{color:var(--teal);font-size:15px;font-weight:600}
.feature p{color:var(--muted);font-size:12px;border-left:1px solid var(--line);padding-left:0}

/* Services */
.services{background:var(--pale);height:470px;padding-top:48px;text-align:center}
.services .lead{color:var(--muted);margin-top:8px}
.service-grid{display:flex;gap:24px;padding:0 60px;margin-top:30px;text-align:left}
.service-card{width:252px;background:var(--white);position:relative;height:250px}
.service-photo{height:148px}
.service-card h3{color:var(--teal);font-size:15px;font-weight:600;padding:14px 16px 4px}
.service-card p{color:var(--muted);font-size:12px;padding:0 16px;line-height:1.5}
.service-card .fold{position:absolute;right:0;bottom:0;width:0;height:0;border-style:solid;border-width:0 0 22px 22px;border-color:transparent transparent var(--teal-soft) transparent}

/* CTA band */
.cta{height:82px;background:linear-gradient(90deg,var(--teal) 0%,var(--sky) 100%);display:flex;align-items:center;justify-content:space-between;padding:0 60px;color:var(--white)}
.cta p{font-size:15px;font-weight:600;line-height:1.4}
.cta-side{display:flex;align-items:center;gap:22px;font-size:14px}
.btn-outline{border:1px solid var(--white);border-radius:20px;padding:7px 22px;font-size:14px}

/* Testimonials */
.testimonials{height:448px;padding-top:48px;text-align:center}
.testimonials .lead{color:var(--muted);margin-top:8px}
.quote-grid{display:flex;justify-content:space-between;padding:0 110px;margin-top:34px}
.quote{width:270px}
.avatar{width:92px;height:92px;border-radius:50%;margin:0 auto;background:linear-gradient(145deg,#c9b8a8,#7d6a5c)}
.quote p{color:var(--muted);font-size:12px;margin-top:18px;line-height:1.6}
.quote .who{margin-top:10px;font-size:12px;color:var(--muted)}
.quote .who b{color:var(--teal);font-weight:600}

/* Partner names */
.partners{height:120px;border-top:1px solid var(--line);display:flex;align-items:center;justify-content:space-between;padding:0 80px}
.partners span{font-size:24px;font-weight:700;color:#4a5054}

/* Footer */
.site-footer{background:var(--footer);height:316px;color:#b9c0c3;display:flex;flex-direction:column}
.footer-cols{flex:1;display:flex;gap:40px;padding:40px 60px 0}
.footer-col{width:245px}
.footer-col h4{color:var(--teal);font-size:17px;font-weight:400;margin-bottom:12px}
.footer-col ul{list-style:none;font-size:12px;line-height:2}
.footer-col ul li::before{content:"› ";color:var(--teal)}
.footer-col p{font-size:12px}
.news-input{margin-top:12px;width:200px;height:30px;background:#454b4e;color:#8d9497;font-size:12px;padding:6px 10px}
.news-btn{margin-top:8px;width:110px;height:30px;background:var(--teal);color:var(--white);font-size:12px;text-align:center;line-height:30px}
.contact-list{font-size:12px;line-height:1.9}
.socials{display:flex;gap:8px;margin-top:12px}
.socials span{width:24px;height:24px;border-radius:3px;background:var(--teal)}
.socials span:nth-child(2){background:var(--sky)}
.socials span:nth-child(3){background:var(--teal-soft)}
.copyright{height:40px;background:var(--footer-deep);text-align:center;line-height:40px;font-size:12px;color:#8d9497}
</style>
</head>
<body>

<section class="hero">
  <div class="hero-photo" role="img" aria-label="Photograph of a desk with paperwork and a pen, softly blurred"></div>
  <div class="hero-shade"></div>
  <header class="site-header">
    <div class="brand">
      <div class="brand-name">Dornaby</div>
      <div class="brand-tag">Bookkeeping</div>
    </div>
    <nav class="main-nav">
      <a class="active" href="#">Home</a>
      <a href="#">About Us</a>
      <a href="#">Services</a>
      <a href="#">Experience</a>
      <a href="#">Resources</a>
      <a href="#">Contact Us</a>
    </nav>
  </header>
  <div class="hero-copy">
    <h1>Accounting and Bookkeeping Services and Support</h1>
    <p>For small and growing organizations in San Diego North County</p>
    <span class="btn-hero">Request your free Consultation</span>
  </div>
</section>

<section class="about">
  <div class="about-text">
    <h2 class="section-title">About <span class="accent">Dornaby Bookkeeping</span></h2>
    <p>We keep the books of small and growing companies clear, current and ready for every decision. Our team sets up tidy records, reconciles accounts each month and sends simple reports you can read in minutes. You always know where your money goes and what comes next for your business.</p>
    <p>For owners who need more than bookkeeping, our senior CPA gives practical advice on cash flow, budgets, tax planning and growth. We work with startups and established firms across North County, in person or remotely, and we keep our fees plain and predictable.</p>
    <span class="btn-small">Learn more</span>
  </div>
  <div class="features">
    <div class="feature">
      <div class="feature-icon"><svg width="22" height="22" viewBox="0 0 24 24" fill="none" stroke="#fff" stroke-width="2.5"><path d="M4 12l5 5L20 6"/></svg></div>
      <div><h3>Reliable</h3><p>Monthly books closed on time, every time, so your numbers are always ready when you need them.</p></div>
    </div>
    <div class="feature">
      <div class="feature-icon"><svg width="22" height="22" viewBox="0 0 24 24" fill="none" stroke="#fff" stroke-width="2.2"><circle cx="12" cy="9" r="5"/><path d="M8 13l-2 8 6-3 6 3-2-8"/></svg></div>
      <div><h3>Experienced</h3><p>Many years of senior finance work behind every answer we give to your business questions.</p></div>
    </div>
    <div class="feature">
      <div class="feature-icon"><svg width="22" height="22" viewBox="0 0 24 24" fill="none" stroke="#fff" stroke-width="2.2"><path d="M12 3l8 3v6c0 5-4 8-8 9-4-1-8-4-8-9V6z"/><path d="M8.5 12l2.5 2.5 4.5-5"/></svg></div>
      <div><h3>Qualified</h3><p>A licensed CPA reviews your accounts and gives advice you can rely on with confidence.</p></div>
    </div>
  </div>
</section>

<section class="services">
  <h2 class="section-title">Our Bookkeeping <span class="accent">Services</span></h2>
  <p class="lead">We provide bookkeeping services specializing in LedgerDesk at your offices or remotely from ours</p>
  <div class="service-grid">
    <div class="service-card">
      <div class="service-photo" role="img" aria-label="Photograph of a ledger binder on a desk" style="background:linear-gradient(135deg,#c8c2b4,#8a8476)"></div>
      <h3>Bookkeeping Services</h3>
      <p>Accurate monthly records, bank reconciliations and payables kept in order for you.</p>
      <span class="fold"></span>
    </div>
    <div class="service-card">
      <div class="service-photo" role="img" aria-label="Photograph of hands working with a calculator and papers" style="background:linear-gradient(135deg,#d9d4cc,#9b948a)"></div>
      <h3>Accounting Services</h3>
      <p>Financial statements, year end close and tax ready reports prepared by a CPA.</p>
      <span class="fold"></span>
    </div>
    <div class="service-card">
      <div class="service-photo" role="img" aria-label="Photograph of an advisor meeting with a client" style="background:linear-gradient(135deg,#b9c4c8,#6f7b80)"></div>
      <h3>Financial Advice</h3>
      <p>Guidance on cash flow, pricing, budgets and funding from senior experience.</p>
      <span class="fold"></span>
    </div>
    <div class="service-card">
      <div class="service-photo" role="img" aria-label="Photograph of a team reviewing charts at a table" style="background:linear-gradient(135deg,#c4c9cc,#7c8488)"></div>
      <h3>Management Accounting</h3>
      <p>Clear dashboards and forecasts that help owners plan the next steps of growth.</p>
      <span class="fold"></span>
    </div>
  </div>
</section>

<section class="cta">
  <p>Our people &amp; technology will take the pain out of your accounting<br>&amp; bookkeeping, letting you get back to business.</p>
  <div class="cta-side">
    <span>Call Us : +1 760 555 0142</span>
    <span class="btn-outline">Contact us Now!</span>
  </div>
</section>

<section class="testimonials">
  <h2 class="section-title">Our Clients <span class="accent">Love Us</span></h2>
  <p class="lead">Owners across North County trust us with their books and plans, here is what a few of them say</p>
  <div class="quote-grid">
    <div class="quote">
      <div class="avatar" role="img" aria-label="Portrait photo of a client"></div>
      <p>“Our books were a mess before we called them. Now every month closes on time and I finally understand my numbers.”</p>
      <div class="who"><b>Dana Whitcombe</b>, Medical</div>
    </div>
    <div class="quote">
      <div class="avatar" role="img" aria-label="Portrait photo of a client" style="background:linear-gradient(145deg,#c7bfb6,#6e6660)"></div>
      <p>“Their advice on cash flow helped us through our first big year. Friendly, quick and always clear in every answer.”</p>
      <div class="who"><b>Luis Ferrano</b>, Businessman</div>
    </div>
    <div class="quote">
      <div class="avatar" role="img" aria-label="Portrait photo of a client" style="background:linear-gradient(145deg,#d2c0ae,#85705e)"></div>
      <p>“Simple reports, fair prices and a real CPA to call when it matters. I recommend them to every founder I know.”</p>
      <div class="who"><b>Priya Holloway</b>, The Law Office</div>
    </div>
  </div>
</section>

<section class="partners" aria-label="Clients">
  <span>Tallwind</span>
  <span>Northmere</span>
  <span>Ostrel</span>
  <span>Bramford</span>
  <span>Kestory</span>
  <span>Pellcraft</span>
</section>

<footer class="site-footer">
  <div class="footer-cols">
    <div class="footer-col">
      <h4>Quick Link</h4>
      <ul><li>Home</li><li>About Us</li><li>Services</li><li>Experience</li><li>Resources</li><li>Contact Us</li></ul>
    </div>
    <div class="footer-col">
      <h4>Services</h4>
      <ul><li>Bookkeeping Services</li><li>Accounting Services</li><li>Financial Advice</li><li>Management Accounting</li></ul>
    </div>
    <div class="footer-col">
      <h4>Get our Newsletter</h4>
      <p>Sign up for simple tips on bookkeeping and news for small business owners.</p>
      <div class="news-input">Enter Your Email</div>
      <div class="news-btn">Subscribe</div>
    </div>
    <div class="footer-col">
      <h4>Our Services</h4>
      <div class="contact-list">
        <div>2140 Harbor View Road, Oceanside</div>
        <div>CA 92054</div>
        <div>Phone : +1 760 555 0142</div>
        <div>Email : info@dornabybookkeeping.com</div>
      </div>
      <div class="socials"><span></span><span></span><span></span></div>
    </div>
  </div>
  <div class="copyright">Copyright © 2016. Dornaby Bookkeeping. All Rights Reserved.</div>
</footer>

</body>
</html>
```